Business card for Eyelash extension salon in Beverly Hills,California USA

We need new business card for our salon in Beverly Hills. The salon name is 'Lashvera' . We would like to have...Business name: Lashvera Name of person: will provide later Address 4720 N.Alder Crest Ave Westbrook Hills , CA 90417 Phone: will provide later (Text only) Web: www.lashverastudio.example Snapgrid icon, Circlebook icon follow us for seasonal campaign and news @lashverastudiolounge Design should look elegant, high-end, clean, simple, cohesive with my brand. Please refer my brand board. Business name color will be metallic bronzy color. Im thinking grey background or white background. Thanks

Target Market(s)

25-35. Gender neutral. People who are in Entertainment business industry.
This is High-end Eyelash extension salon in Beverly Hills

Industry/Entity Type

Beauty Salon

Contact Information for Business Card

Business name: Lashvera
Name of person: will provide later
Address 4720 N.Alder Crest Ave Westbrook Hills , CA 90417
Phone: will provide later (Text only)
Web: www.lashverastudio.example
Snapgrid icon, Circlebook icon
follow us for seasonal campaign and news @lashverastudiolounge

Requirements
Must have
• Beautiful, elegant, clean and simple look but very attractive and modern
Should not have
• We don't like too clutter, too busy designs.

```html
<!DOCTYPE html>
<html lang="en">
<head>
<meta charset="utf-8">
<title>Lashvera Business Card</title>
<link rel="stylesheet" href="https://fonts.googleapis.com/css2?family=Open+Sans:ital,wght@0,300;0,400;0,700;1,600&display=swap">
<style>
  :root {
    --backdrop: #b9b9b9;
    --card: #1f1f1f;
    --bronze: #a0735a;
    --ink: #f2f2f2;
    --rule: #5a5a5a;
  }
  * { box-sizing: border-box; margin: 0; padding: 0; }
  html, body {
    width: 1200px; height: 1200px; overflow: hidden;
    background: var(--backdrop);
    font-family: "Open Sans", sans-serif;
  }
  .canvas { position: relative; width: 1200px; height: 1200px; }
  .card {
    position: absolute; top: 310px;
    width: 366px; height: 594px;
    background: var(--card);
    text-align: center; color: var(--ink);
  }
  .card--front { left: 233px; }
  .card--back { left: 628px; }
  .brand-name {
    position: absolute; left: 0; right: 0;
    font-family: "Open Sans", sans-serif;
    font-weight: 300; font-size: 64px; letter-spacing: 1px;
    color: var(--bronze);
  }
  .card--front .brand-name { top: 145px; }
  .card--back .brand-name { top: 170px; }
  .person-name {
    position: absolute; top: 370px; left: 0; right: 0;
    font-weight: 700; font-size: 20px; color: var(--bronze);
  }
  .rule {
    position: absolute; left: 113px; width: 140px; height: 1px;
    background: var(--rule);
  }
  .rule--upper { top: 408px; }
  .rule--lower { top: 480px; }
  .contact {
    position: absolute; left: 0; right: 0;
    font-size: 16px; line-height: 21px; font-weight: 400;
  }
  .contact--address { top: 424px; }
  .contact--reach { top: 497px; }
  .social-row {
    position: absolute; top: 474px; left: 66px; right: 66px;
    display: flex; align-items: center; justify-content: center; gap: 8px;
  }
  .social-row .line { flex: 1; height: 1px; background: var(--rule); }
  .social-item { display: flex; align-items: center; gap: 4px; font-size: 12px; }
  .social-item .dot {
    width: 10px; height: 10px; border-radius: 50%; background: var(--ink);
  }
  .follow {
    position: absolute; top: 502px; left: 0; right: 0;
    font-size: 16px; line-height: 22px;
  }
  .follow .handle { font-style: italic; font-weight: 600; }
</style>
</head>
<body>
<main class="canvas">
  <section class="card card--front">
    <div class="brand-name">Lashvera</div>
    <div class="person-name">MARISOL KENT</div>
    <div class="rule rule--upper"></div>
    <p class="contact contact--address">4720 N.Alder Crest<br>Ave Westbrook Hills , CA 90417</p>
    <div class="rule rule--lower"></div>
    <p class="contact contact--reach">044-555 019 284<br>www.lashverastudio.example</p>
  </section>

  <section class="card card--back">
    <div class="brand-name">Lashvera</div>
    <div class="social-row">
      <span class="line"></span>
      <span class="social-item"><span class="dot"></span>Circlebook</span>
      <span class="social-item"><span class="dot"></span>Snapgrid</span>
      <span class="line"></span>
    </div>
    <p class="follow">Follow us for seasonal campaign<br>and news <span class="handle">@lashverastudiolounge</span></p>
  </section>
</main>
</body>
</html>
```